Tavenhurst Falcons FC Website

We are looking to develop a new website for Tavenhurst FC. Tavenhurst FC has now joined with Tavenhurst Falcons FC and we are looking at a website that can work for both clubs. Tavenhurst FC play in a local park football competition while tavenhurst Falcons are a Semi Professional team that plays in the Ostral Premier Series Competition. What we are after is two separate website off the one platform. I have attached both team logos for you to visualise. Also you can look at the existing tavenhurst website www.tavenhurstfc.net.au. We are looking for a huge improvement in the website and it will be imperative we have links to sponsors and the sponsors can get regular visuals. Weare looking to move this club forward and have a very professional website that can communicate clearly with the community.

Hi All,

Please remember that the website is to represent two clubs;
1. Tavenhurst Falcons FC (Competes in Semi Professional League)
2. Tavenhurst FC (Compete in KPWLT League which is a lower level)

Further to this the Tavenhurst Falcons FC page will require a player profile page which will show photos of each player and a little bio on each.

Thanks

Reason: Would like to spend more time review existing and new designs

```html
<!DOCTYPE html>
<html lang="en">
<head>
<meta charset="utf-8">
<title>Sponsors – Tavenhurst Falcons FC</title>
<link rel="stylesheet" href="https://fonts.googleapis.com/css2?family=Roboto:wght@400;700&family=Roboto+Condensed:wght@400;700&family=Gelasio:ital,wght@1,400;1,500&display=swap">
<style>
:root{
  --red:#e8231b;
  --red-dark:#c8160f;
  --red-deep:#b3110b;
  --white:#ffffff;
  --page:#f1f1f1;
  --ink:#1b1b1b;
  --muted:#444444;
  --line:#c9c9c9;
  --footer-top:#ececec;
  --footer-bottom:#d9dcde;
  --hero-a:#1a1430;
  --hero-b:#3d2f78;
  --hero-c:#6a58b8;
  --gold:#e6b21c;
  --green:#7cc243;
}
*{box-sizing:border-box;margin:0;padding:0}
html,body{width:722px;height:1200px;overflow:hidden;background:var(--page)}
body{position:relative;font-family:"Roboto",Arial,sans-serif;color:var(--ink)}
a{color:inherit;text-decoration:none}

/* Header */
.site-header{position:absolute;left:0;top:0;width:722px;height:94px;background:var(--red)}
.utility-bar{position:absolute;left:0;top:0;width:722px;height:32px;background:var(--red-dark);border-bottom:1px solid var(--red-deep)}
.utility-link{position:absolute;top:10px;font:700 9px "Roboto",Arial,sans-serif;color:var(--white);letter-spacing:.3px}
.utility-link::after{content:" ▸"}
.utility-divider{position:absolute;top:0;width:1px;height:32px;background:var(--red-deep)}
.follow-label{position:absolute;left:440px;top:10px;font:700 9px "Roboto",Arial,sans-serif;color:var(--white)}
.social-list{position:absolute;left:508px;top:9px;display:flex;gap:10px}
.social-dot{width:13px;height:13px;border-radius:50%;background:var(--white)}
.main-nav a{position:absolute;top:52px;font:700 14px "Roboto",Arial,sans-serif;color:var(--white)}
.main-nav .is-active{top:33px;height:61px;padding:19px 10px 0;background:var(--red-deep)}
.search-icon{position:absolute;left:676px;top:50px}

.club-mark{position:absolute;left:313px;top:0;width:96px;height:106px;background:var(--white);display:flex;flex-direction:column;align-items:center;justify-content:center;gap:6px;box-shadow:0 1px 3px rgba(0,0,0,.25)}
.club-mark-dot{width:34px;height:34px;border-radius:50%;background:var(--red)}
.club-mark-name{font:700 12px "Roboto Condensed",sans-serif;color:var(--red);text-align:center;line-height:1.1}

/* Hero */
.hero{position:absolute;left:0;top:94px;width:722px;height:376px;background:radial-gradient(ellipse at 50% 60%,var(--hero-c) 0%,var(--hero-b) 40%,var(--hero-a) 85%)}
.hero-rule{position:absolute;left:0;top:470px;width:722px;height:5px;background:var(--red)}
.hero-badge{position:absolute;left:327px;top:218px;width:68px;height:68px;border-radius:50%;background:var(--red);display:flex;align-items:center;justify-content:center;box-shadow:0 0 0 3px rgba(255,255,255,.15)}
.hero-title{position:absolute;left:175px;top:274px;width:373px;height:60px;background:rgba(20,16,30,.78);color:var(--white);font:italic 400 31px "Gelasio",Georgia,serif;display:flex;align-items:center;justify-content:center}

/* Sponsors */
.tab-strip{position:absolute;left:0;top:475px;width:722px;height:23px;background:#e4e4e4;border-bottom:1px solid #d4d4d4}
.dots{position:absolute;left:345px;top:502px;display:flex;gap:6px}
.dots span{width:5px;height:5px;border-radius:50%;background:var(--ink)}
.section-rule{position:absolute;left:0;top:541px;width:722px;height:1px;background:var(--line)}
.section-title{position:absolute;left:122px;top:529px;width:478px;background:var(--page);text-align:center;font:italic 500 18px "Gelasio",Georgia,serif;letter-spacing:.2px}
.section-sub{position:absolute;left:0;top:551px;width:722px;text-align:center;font:400 11.5px "Gelasio",Georgia,serif;color:var(--muted)}

.sponsor{position:absolute;display:flex;align-items:center;justify-content:center;gap:7px;width:200px;height:80px;font:700 22px "Roboto Condensed",sans-serif}
.sponsor .mark{flex:none}
.sponsor-emberline{left:38px;top:608px;color:#d4176a}
.sponsor-orwell{left:261px;top:608px;color:#4a2e10;font-size:15px;flex-direction:column;gap:4px}
.sponsor-brightsmile{left:483px;top:608px;color:#7a9a2a}
.sponsor-sentratec{left:38px;top:746px;color:#2f9a3c}
.sponsor-corvan{left:261px;top:746px;color:#5b2e8e}
.sponsor-lumora{left:483px;top:746px;color:#1e9aa8;font-size:28px}
.sponsor-tidypro{left:58px;top:868px;width:150px;height:110px;justify-content:flex-start;align-items:flex-end;color:var(--ink);font-size:15px}

.donate{position:absolute;left:521px;top:966px;width:182px;height:52px;background:var(--red);border-radius:9px 9px 0 0;display:flex;align-items:center;justify-content:center;gap:10px;color:var(--white);font:italic 400 25px "Gelasio",Georgia,serif}

/* Footer */
.site-footer{position:absolute;left:0;top:1018px;width:722px;height:182px;border-top:3px solid var(--red);background:linear-gradient(var(--footer-top),var(--footer-bottom))}
.footer-col{position:absolute;top:18px}
.footer-col .icon{position:absolute;top:0}
.footer-heading{position:absolute;top:22px;font:700 17px "Roboto Condensed",sans-serif;color:var(--ink);border-bottom:1px solid #9a9a9a;padding-bottom:6px}
.footer-links{position:absolute;top:58px;list-style:none;font:400 14px "Roboto Condensed",sans-serif;color:#333;line-height:18px}
.col-home{left:48px}
.col-home .footer-heading{left:42px;width:73px}
.col-home .footer-links{left:42px}
.col-club{left:198px}
.col-club .footer-heading{left:46px;width:70px}
.col-club .footer-links{left:46px}
.col-fixtures{left:344px}
.col-fixtures .footer-heading{left:54px;width:270px}
.col-fixtures .footer-links{left:54px;width:270px}
.col-fixtures li{display:flex;justify-content:space-between}
.copyright{position:absolute;left:0;top:1186px;width:722px;height:14px;background:var(--red);color:var(--white);font:400 8px "Roboto",Arial,sans-serif;padding:3px 0 0 90px}
</style>
</head>
<body>

<header class="site-header">
  <div class="utility-bar">
    <a class="utility-link" style="left:90px" href="#">JOIN US NOW</a>
    <span class="utility-divider" style="left:176px"></span>
    <a class="utility-link" style="left:200px" href="#">GET YOUR TICKETS</a>
    <span class="utility-divider" style="left:300px"></span>
    <span class="utility-divider" style="left:420px"></span>
    <span class="follow-label">FOLLOW US :</span>
    <div class="social-list" aria-label="Social links">
      <span class="social-dot"></span><span class="social-dot"></span><span class="social-dot"></span><span class="social-dot"></span>
    </div>
  </div>
  <nav class="main-nav">
    <a href="#" style="left:26px">Home</a>
    <a href="#" style="left:89px">Photo Gallery</a>
    <a href="#" style="left:192px">Fixture &amp; Results</a>
    <a href="#" style="left:422px">News</a>
    <a href="#" class="is-active" style="left:468px">Sponsor</a>
    <a href="#" style="left:546px">Club</a>
    <a href="#" style="left:596px">Contact Us</a>
  </nav>
  <svg class="search-icon" width="18" height="18" viewBox="0 0 18 18" aria-label="Search"><circle cx="7" cy="7" r="5.5" fill="none" stroke="#fff" stroke-width="2"/><line x1="11" y1="11" x2="16.5" y2="16.5" stroke="#fff" stroke-width="2.4" stroke-linecap="round"/></svg>
</header>

<a class="club-mark" href="#">
  <span class="club-mark-dot"></span>
  <span class="club-mark-name">Tavenhurst FC</span>
</a>

<section class="hero" role="img" aria-label="Night view of a lit stadium with fireworks above the roof"></section>
<div class="hero-badge">
  <svg width="26" height="36" viewBox="0 0 26 36" aria-hidden="true"><polygon points="8,0 18,0 15,6 11,6" fill="#fff"/><polygon points="11,7 15,7 20,28 13,36 6,28" fill="#fff"/></svg>
</div>
<h1 class="hero-title">·Our Generous Sponsors·</h1>
<div class="hero-rule"></div>

<main>
  <div class="tab-strip"></div>
  <div class="dots"><span></span><span></span><span></span></div>
  <div class="section-rule"></div>
  <h2 class="section-title">WE ARE GRATEFUL TO THE FOLLOWING SPONSORS</h2>
  <p class="section-sub">who actively support us and our activities</p>

  <a class="sponsor sponsor-emberline" href="#"><span class="mark" style="width:20px;height:20px;background:#d4176a"></span>Emberline</a>
  <a class="sponsor sponsor-orwell" href="#"><span class="mark" style="width:56px;height:50px;background:#5a3a14"></span>Orwell Tax Services</a>
  <a class="sponsor sponsor-brightsmile" href="#">Brightsmile Care</a>
  <a class="sponsor sponsor-sentratec" href="#"><span class="mark" style="width:22px;height:22px;border-radius:50%;background:#e0473a"></span>Sentratec</a>
  <a class="sponsor sponsor-corvan" href="#"><span class="mark" style="width:40px;height:40px;border-radius:50%;background:#f0b21a"></span>Corvan Finance</a>
  <a class="sponsor sponsor-lumora" href="#">Lumora</a>
  <a class="sponsor sponsor-tidypro" href="#"><span class="mark" style="width:36px;height:110px;background:#4f7fc0;border:1px solid #2b4f85"></span>Tidypro</a>

  <a class="donate" href="#">
    <svg width="22" height="14" viewBox="0 0 22 14" aria-hidden="true"><rect x="1" y="1" width="20" height="12" rx="1.5" fill="none" stroke="#fff" stroke-width="1.6"/><circle cx="11" cy="7" r="3" fill="#fff"/></svg>
    DONATE
  </a>
</main>

<footer class="site-footer">
  <div class="footer-col col-home">
    <svg class="icon" width="36" height="42" viewBox="0 0 36 42" aria-hidden="true"><path d="M7 2h22v10c0 8-5 13-11 13S7 20 7 12z" fill="var(--gold)"/><path d="M7 5H2c0 7 3 10 6 10M29 5h5c0 7-3 10-6 10" fill="none" stroke="var(--gold)" stroke-width="2.5"/><rect x="15" y="25" width="6" height="8" fill="var(--gold)"/><rect x="9" y="33" width="18" height="6" rx="1" fill="#c98f10"/></svg>
    <h3 class="footer-heading">HOME</h3>
    <ul class="footer-links"><li>News</li><li>Gallery</li><li>Sponsor</li><li>Contact Us</li></ul>
  </div>
  <div class="footer-col col-club">
    <svg class="icon" width="38" height="38" viewBox="0 0 38 38" aria-hidden="true"><circle cx="19" cy="19" r="17" fill="#fff" stroke="#222" stroke-width="2"/><polygon points="19,12 25,16.5 23,23.5 15,23.5 13,16.5" fill="#222"/><circle cx="6" cy="12" r="3.5" fill="#222"/><circle cx="32" cy="12" r="3.5" fill="#222"/><circle cx="10" cy="31" r="3.5" fill="#222"/><circle cx="28" cy="31" r="3.5" fill="#222"/></svg>
    <h3 class="footer-heading">CLUB</h3>
    <ul class="footer-links"><li>History</li><li>Committee</li><li>Awards</li><li>Forms</li></ul>
  </div>
  <div class="footer-col col-fixtures">
    <svg class="icon" width="40" height="36" viewBox="0 0 40 36" aria-hidden="true"><polygon points="8,4 32,4 39,34 1,34" fill="var(--green)"/><line x1="20" y1="4" x2="20" y2="34" stroke="#fff" stroke-width="1.5"/><line x1="5" y1="19" x2="35" y2="19" stroke="#fff" stroke-width="1.5"/><circle cx="20" cy="19" r="5" fill="none" stroke="#fff" stroke-width="1.5"/></svg>
    <h3 class="footer-heading">FIXTURES &amp; RESULTS</h3>
    <ul class="footer-links">
      <li><span>Premier League</span><span>Under 10 / 2</span></li>
      <li><span>Premier League</span><span>Under 10 / 3</span></li>
      <li><span>ResSuper League</span><span>Under 11 / 1</span></li>
      <li><span>Super League Res</span><span>Under 12 / 3</span></li>
    </ul>
  </div>
</footer>
<p class="copyright">© 2012-2013 All Rights Reserved to Tavenhurst Falcons FC</p>

</body>
</html>
```